Logo, Web and Mobile Designs for enterprise social media platform

All the details are in the attached document, please start reading the scope document first which explains what is this project about and the details about the needed deliverables, after that please read the UI_Requirements document which will detail what is expected regarding the coded web version since this is a coded contest, it is very important that you meet the UI requirements or suggest something else but we will need to agree first before working on the coded version

Good Luck

Target Market(s)

Enterprise Social Media

Industry/Entity Type

Media

Coding

Coded - Design and coding required

Number of Pages Required

5+ page

Font styles to use
Sans Serif

Requirements
Must have
• All the must haves are listed in the scope document so please check before you start

```html
<!DOCTYPE html>
<html lang="en">
<head>
<meta charset="utf-8">
<title>Teamvera – Track Details</title>
<link rel="stylesheet" href="https://fonts.googleapis.com/css2?family=Open+Sans:wght@400;600;700&display=swap">
<style>
:root{
  --page-bg:#eceef1;
  --header-bg:#ffffff;
  --line:#dfe2e6;
  --item-bg:#f3f4f6;
  --item-text:#3d4550;
  --accent:#1b8ac6;
  --footer-bg:#2b8dbf;
  --card-head:#f1f2f4;
  --muted:#555c66;
  --white:#ffffff;
}
*{box-sizing:border-box;margin:0;padding:0}
html,body{width:1200px;height:3420px;overflow:hidden}
body{position:relative;background:var(--page-bg);font-family:"Open Sans",Arial,sans-serif;color:var(--item-text)}
.site-header{position:absolute;left:0;top:0;width:1200px;height:240px;background:var(--header-bg);border-bottom:4px solid var(--line);display:flex;align-items:center;justify-content:center}
.header-btn{position:absolute;top:0;width:220px;height:236px;display:flex;align-items:center;justify-content:center}
.header-btn.home{left:0;border-right:4px solid var(--line)}
.header-btn.menu{right:0;border-left:4px solid var(--line)}
.brand-name{font-size:80px;font-weight:600;color:var(--accent);letter-spacing:1px}
.nav{position:absolute;left:48px;width:1104px;list-style:none}
.nav-item{height:150px;background:var(--item-bg);border-bottom:4px solid #e6e8eb;border-left:4px solid #e1e3e6;display:flex;align-items:center;padding-left:68px;position:relative;font-size:42px;text-transform:uppercase}
.nav-item .ico{width:64px;display:flex;align-items:center;margin-right:28px}
.nav-item .caret{position:absolute;right:48px;top:50%;transform:translateY(-50%)}
.nav-top{top:312px}
.nav-bottom{top:2088px}
.track-panel{position:absolute;left:48px;top:1060px;width:1104px;height:1028px;background:var(--white);border-left:4px solid #e1e3e6}
.card{position:absolute;left:40px;top:88px;width:1020px;height:860px;border:4px solid #e6e8eb;background:var(--white)}
.card-head{height:140px;background:var(--card-head);border-bottom:4px solid #e6e8eb;display:flex;align-items:center;padding-left:64px;gap:24px;font-size:48px;font-weight:600;text-transform:uppercase}
.field-label{position:absolute;left:60px;top:228px;font-size:40px;color:#333}
.field-input{position:absolute;left:60px;top:300px;width:896px;height:112px;border:4px solid #dcdfe3;padding-left:36px;display:flex;align-items:center;font-size:32px;color:#222}
.actions{position:absolute;left:60px;top:472px;display:flex;align-items:center}
.btn-save{width:432px;height:104px;background:var(--accent);color:var(--white);font-size:44px;font-weight:600;display:flex;align-items:center;justify-content:center;text-transform:uppercase;border-radius:6px}
.btn-link{font-size:40px;color:#333;text-transform:uppercase;margin-left:60px}
.list-label{position:absolute;left:60px;top:640px;font-size:40px;color:#333}
.list-entry{position:absolute;left:76px;top:744px;font-size:30px;color:#222}
.site-footer{position:absolute;left:0;top:3052px;width:1200px;height:368px;background:var(--footer-bg);color:var(--white);text-align:center}
.social{display:flex;justify-content:center;gap:28px;margin-top:64px}
.social span{width:64px;height:64px;background:var(--white);border-radius:10px}
.footer-links{margin-top:34px;font-size:32px;font-weight:600}
.copyright{margin-top:26px;font-size:32px}
</style>
</head>
<body>
<header class="site-header">
  <div class="header-btn home">
    <svg width="64" height="56" viewBox="0 0 16 14"><path d="M8 0 0 7h2v7h4.5V9.5h3V14H14V7h2z" fill="#555c66"/></svg>
  </div>
  <div class="brand"><span class="brand-name">Teamvera</span></div>
  <div class="header-btn menu">
    <svg width="60" height="52" viewBox="0 0 15 13"><rect y="0" width="15" height="2.6" fill="#555c66"/><rect y="5.2" width="15" height="2.6" fill="#555c66"/><rect y="10.4" width="15" height="2.6" fill="#555c66"/></svg>
  </div>
</header>

<ul class="nav nav-top">
  <li class="nav-item"><span class="ico"><svg width="44" height="44" viewBox="0 0 10 10"><rect width="4.5" height="4.5" fill="#1b8ac6"/><rect x="5.5" width="4.5" height="4.5" fill="#1b8ac6"/><rect y="5.5" width="4.5" height="4.5" fill="#1b8ac6"/><rect x="5.5" y="5.5" width="4.5" height="4.5" fill="#1b8ac6"/></svg></span>View Dashboard</li>
  <li class="nav-item"><span class="ico"><svg width="44" height="44" viewBox="0 0 10 10"><rect x=".5" y="1.5" width="9" height="8" fill="none" stroke="#1b8ac6"/><rect x=".5" y="1.5" width="9" height="2" fill="#1b8ac6"/><rect x="2" y="0" width="1" height="2.5" fill="#1b8ac6"/><rect x="7" y="0" width="1" height="2.5" fill="#1b8ac6"/><g fill="#1b8ac6"><rect x="2" y="5" width="1.4" height="1.2"/><rect x="4.3" y="5" width="1.4" height="1.2"/><rect x="6.6" y="5" width="1.4" height="1.2"/><rect x="2" y="7.2" width="1.4" height="1.2"/><rect x="4.3" y="7.2" width="1.4" height="1.2"/></g></svg></span>View Event<svg class="caret" width="28" height="28" viewBox="0 0 10 10"><path d="M1 5 5 1.5 9 5M1 9 5 5.5 9 9" fill="none" stroke="#666" stroke-width="1.4"/></svg></li>
  <li class="nav-item"><span class="ico"><svg width="22" height="30" viewBox="0 0 6 10"><path d="M1 1 5 5 1 9" fill="none" stroke="#1b8ac6" stroke-width="1.5"/></svg></span>About Us<svg class="caret" width="28" height="28" viewBox="0 0 10 10"><path d="M1 5 5 1.5 9 5M1 9 5 5.5 9 9" fill="none" stroke="#666" stroke-width="1.4"/></svg></li>
  <li class="nav-item"><span class="ico"><svg width="22" height="30" viewBox="0 0 6 10"><path d="M1 1 5 5 1 9" fill="none" stroke="#1b8ac6" stroke-width="1.5"/></svg></span>Speakers<svg class="caret" width="28" height="28" viewBox="0 0 10 10"><path d="M1 5 5 1.5 9 5M1 9 5 5.5 9 9" fill="none" stroke="#666" stroke-width="1.4"/></svg></li>
  <li class="nav-item"><span class="ico"><svg width="22" height="30" viewBox="0 0 6 10"><path d="M1 1 5 5 1 9" fill="none" stroke="#1b8ac6" stroke-width="1.5"/></svg></span>Track<svg class="caret" width="28" height="28" viewBox="0 0 10 10"><path d="M1 1 5 4.5 9 1M1 5 5 8.5 9 5" fill="none" stroke="#666" stroke-width="1.4"/></svg></li>
</ul>

<section class="track-panel">
  <div class="card">
    <div class="card-head">
      <svg width="52" height="36" viewBox="0 0 13 9"><rect x="0" y="0" width="8" height="6.5" fill="#555c66"/><path d="M8.5 2h2.5l2 2.5v2h-4.5z" fill="#555c66"/><circle cx="2.5" cy="7.5" r="1.4" fill="#555c66"/><circle cx="10.5" cy="7.5" r="1.4" fill="#555c66"/></svg>
      Track Details
    </div>
    <div class="field-label">Track Name :</div>
    <div class="field-input">Computer Vision</div>
    <div class="actions">
      <div class="btn-save">Save Track</div>
      <div class="btn-link">Reset</div>
      <div class="btn-link" style="margin-left:48px">Cancel</div>
    </div>
    <div class="list-label">Tracks List :</div>
    <div class="list-entry">Computer Vision</div>
  </div>
</section>

<ul class="nav nav-bottom">
  <li class="nav-item"><span class="ico"><svg width="22" height="30" viewBox="0 0 6 10"><path d="M1 1 5 5 1 9" fill="none" stroke="#1b8ac6" stroke-width="1.5"/></svg></span>Sessions<svg class="caret" width="28" height="28" viewBox="0 0 10 10"><path d="M1 5 5 1.5 9 5M1 9 5 5.5 9 9" fill="none" stroke="#666" stroke-width="1.4"/></svg></li>
  <li class="nav-item"><span class="ico"><svg width="22" height="30" viewBox="0 0 6 10"><path d="M1 1 5 5 1 9" fill="none" stroke="#1b8ac6" stroke-width="1.5"/></svg></span>Organizers<svg class="caret" width="28" height="28" viewBox="0 0 10 10"><path d="M1 5 5 1.5 9 5M1 9 5 5.5 9 9" fill="none" stroke="#666" stroke-width="1.4"/></svg></li>
  <li class="nav-item"><span class="ico"><svg width="22" height="30" viewBox="0 0 6 10"><path d="M1 1 5 5 1 9" fill="none" stroke="#1b8ac6" stroke-width="1.5"/></svg></span>Sponsors<svg class="caret" width="28" height="28" viewBox="0 0 10 10"><path d="M1 5 5 1.5 9 5M1 9 5 5.5 9 9" fill="none" stroke="#666" stroke-width="1.4"/></svg></li>
  <li class="nav-item"><span class="ico"><svg width="22" height="30" viewBox="0 0 6 10"><path d="M1 1 5 5 1 9" fill="none" stroke="#1b8ac6" stroke-width="1.5"/></svg></span>Exhibitor<svg class="caret" width="28" height="28" viewBox="0 0 10 10"><path d="M1 5 5 1.5 9 5M1 9 5 5.5 9 9" fill="none" stroke="#666" stroke-width="1.4"/></svg></li>
  <li class="nav-item"><span class="ico"><svg width="22" height="30" viewBox="0 0 6 10"><path d="M1 1 5 5 1 9" fill="none" stroke="#1b8ac6" stroke-width="1.5"/></svg></span>Security<svg class="caret" width="28" height="28" viewBox="0 0 10 10"><path d="M1 5 5 1.5 9 5M1 9 5 5.5 9 9" fill="none" stroke="#666" stroke-width="1.4"/></svg></li>
  <li class="nav-item"><span class="ico"><svg width="22" height="30" viewBox="0 0 6 10"><path d="M1 1 5 5 1 9" fill="none" stroke="#1b8ac6" stroke-width="1.5"/></svg></span>Members<svg class="caret" width="28" height="28" viewBox="0 0 10 10"><path d="M1 5 5 1.5 9 5M1 9 5 5.5 9 9" fill="none" stroke="#666" stroke-width="1.4"/></svg></li>
</ul>

<footer class="site-footer">
  <div class="social"><span></span><span></span><span></span><span></span><span></span></div>
  <div class="footer-links">Home &nbsp;/&nbsp; Contact &nbsp;/&nbsp; Topics &nbsp;/&nbsp; Posts &amp; Comments &nbsp;/&nbsp; Videos Links</div>
  <div class="copyright">Copyright @ 2015 - 2015.Teamvera. All Rights Reserved.</div>
</footer>
</body>
</html>
```